Awesome business card design needed

We need a new business card design to go with our new logo.
We are a web development agency that specialises in highly complex back-end integrations as opposed to design, our customers are retailers, hotels, hospitals and any other organisation that has a large online marketing department.
Take a look at our website - www.brenoloft.com for some inspiration.
We want our new business cards to exude class, professionalism and style.
We are likely to choose a high-end card to print them on but we want the design of the card itself to really turn heads.
We have no specific colour requirements, the logo as you will see is a turquoise colour R89 G171 B167 #59aba7 but it can also be in white if you want to make the colour of the card something different.
The information on the card should be:
Name
Position
Tel
email
Potentially a double sided card could have our web address, twitter and FB links.

```html
<!DOCTYPE html>
<html lang="en">
<head>
<meta charset="utf-8">
<title>Brenoloft business card</title>
<link rel="stylesheet" href="https://fonts.googleapis.com/css2?family=Michroma&family=Archivo:wght@400;700&display=swap">
<style>
  :root {
    --teal: #59aba7;
    --ink: #333333;
    --charcoal: #2e2e2e;
    --paper: #ffffff;
    --stage: #ececec;
    --rule: #c9c9c9;
  }
  * { margin: 0; padding: 0; box-sizing: border-box; }
  html, body { width: 1200px; height: 720px; overflow: hidden; }
  body {
    background: var(--stage);
    display: flex;
    align-items: center;
    justify-content: center;
    gap: 40px;
    font-family: "Michroma", sans-serif;
  }
  .card {
    position: relative;
    width: 540px;
    height: 310px;
    overflow: hidden;
    box-shadow: 0 2px 8px rgba(0,0,0,0.12);
  }
  .card--front { background: var(--paper); color: var(--ink); }
  .card--back { background: var(--teal); color: var(--paper); }

  .wordmark {
    position: absolute;
    left: 0; right: 0;
    text-align: center;
    font-family: "Michroma", sans-serif;
    font-weight: 400;
    letter-spacing: 2px;
  }
  .card--front .wordmark { top: 42px; font-size: 56px; color: var(--teal); }
  .card--back .wordmark { top: 88px; font-size: 60px; color: var(--paper); }

  .identity {
    position: absolute;
    right: 232px;
    top: 160px;
    text-align: right;
    font-size: 11px;
    line-height: 1.45;
  }
  .identity__name { font-family: "Archivo", sans-serif; font-weight: 700; font-size: 18px; line-height: 1.1; }
  .identity__position { font-family: "Archivo", sans-serif; color: var(--teal); font-size: 14px; margin-bottom: 4px; }

  .divider {
    position: absolute;
    left: 322px;
    top: 160px;
    width: 1px;
    height: 78px;
    background: var(--rule);
  }

  .contacts {
    position: absolute;
    left: 334px;
    top: 160px;
    list-style: none;
    font-size: 11px;
    line-height: 25px;
  }
  .contacts li { display: flex; align-items: center; gap: 7px; }
  .contacts svg { width: 12px; height: 12px; flex: none; }

  .card__bands { position: absolute; left: 0; bottom: 0; width: 540px; height: 60px; }

  .social {
    position: absolute;
    left: 0; right: 0;
    top: 200px;
    display: flex;
    justify-content: center;
    align-items: center;
    gap: 8px;
    font-family: "Archivo", sans-serif;
    font-weight: 700;
    font-size: 18px;
  }
  .social__label { margin-right: 4px; }
  .social__badge { width: 28px; height: 28px; border-radius: 5px; background: var(--paper); opacity: 0.9; }
  .website {
    position: absolute;
    left: 0; right: 0;
    top: 246px;
    text-align: center;
    font-family: "Archivo", sans-serif;
    font-size: 17px;
    letter-spacing: 2px;
  }
  .website strong { font-weight: 700; }
</style>
</head>
<body>
  <section class="card card--front" aria-label="Card front">
    <div class="wordmark">brenoloft</div>

    <div class="identity">
      <div class="identity__name">Your Name</div>
      <div class="identity__position">Position</div>
      <div>Street Name, City Name</div>
      <div>State Zip Code</div>
    </div>

    <div class="divider"></div>

    <ul class="contacts">
      <li>
        <svg viewBox="0 0 12 12"><circle cx="6" cy="6" r="6" fill="var(--teal)"/><path d="M4 3.2l1.2 1.4-.7.8a4 4 0 0 0 2.1 2.1l.8-.7 1.4 1.2-.8 1A5 5 0 0 1 3 4z" fill="#fff"/></svg>
        123-456-7890
      </li>
      <li>
        <svg viewBox="0 0 12 12"><circle cx="6" cy="6" r="6" fill="var(--teal)"/><rect x="3" y="4" width="6" height="4.2" fill="#fff"/><path d="M3 4l3 2.3L9 4" fill="none" stroke="var(--teal)" stroke-width=".8"/></svg>
        info@brenoloft.com
      </li>
      <li>
        <svg viewBox="0 0 12 12"><circle cx="6" cy="6" r="6" fill="var(--teal)"/><circle cx="6" cy="6" r="3.2" fill="none" stroke="#fff" stroke-width=".8"/><path d="M2.8 6h6.4M6 2.8v6.4" stroke="#fff" stroke-width=".8"/></svg>
        www.brenoloft.com
      </li>
    </ul>

    <svg class="card__bands" viewBox="0 0 540 60" aria-hidden="true">
      <polygon points="0,38 350,38 340,60 0,60" fill="var(--charcoal)"/>
      <polygon points="320,60 352,30 540,14 540,60" fill="var(--teal)"/>
    </svg>
  </section>

  <section class="card card--back" aria-label="Card back">
    <div class="wordmark">brenoloft</div>
    <div class="social">
      <span class="social__label">Follow Us On:</span>
      <span class="social__badge"></span>
      <span class="social__badge"></span>
    </div>
    <div class="website">www.<strong>brenoloft</strong>.com</div>
  </section>
</body>
</html>
```